We need a laundry sheet packingbox desgin

-look at our website lindavel.nl to be in line with our house style/collor
We are a perfume seller and would like to offer also wasshingsheets with NO SMELL, so the customers can buy this incombination with our washingperfumes.
-the wassingheets will be neutrale(NO SMELL)
-it will be for the Dutch market
The next points should be on the desgin of the package
-our brand name: LINDAVEL
-product name: WASSTRIPS
-(contains) Bevat: 30 wasstrips
-30 wasstrips = 60 wasbeurten
Please take some inspiration of others sellers & regarding eco friendly symbols etc.:
voltirra.com & plomkens.nl
Backside information will be provided afther we found the right desgin
Please look at attachement pdf open box.
Here you can find the pdf design where you need to customize:
https://fz.qx/t-kR8bNwL2sY

```html
<!DOCTYPE html>
<html lang="nl">
<head>
<meta charset="utf-8">
<title>LINDAVEL Wasstrips – verpakking voorzijde</title>
<link href="https://fonts.googleapis.com/css2?family=Cormorant+Garamond:wght@600&family=Titan+One&family=Roboto+Condensed:wght@400;500&display=swap" rel="stylesheet">
<style>
  :root{
    --stage:#e4e6e8;
    --royal:#2b3aa8;
    --royal-deep:#1d2a8c;
    --sky:#4fa8f0;
    --gold:#d9a53a;
    --white:#f4f5f2;
    --crimson:#a3283b;
    --crimson-dark:#7e1a2b;
    --band:#1f2226;
    --mint:#3fbf7f;
    --teal:#1fa39a;
    --icon:#e9ecef;
  }
  *{box-sizing:border-box;margin:0;padding:0}
  html,body{width:1200px;height:1062px;overflow:hidden;background:var(--stage)}
  .package-front{
    position:absolute;left:250px;top:26px;width:700px;height:1010px;
    background:
      radial-gradient(ellipse 60% 32% at 50% 46%, rgba(255,255,255,.95) 0%, rgba(170,220,255,.55) 22%, rgba(60,120,230,0) 60%),
      linear-gradient(180deg,var(--royal-deep) 0%,var(--royal) 30%,#2f5fd0 50%,var(--royal) 75%,var(--royal-deep) 100%);
    overflow:hidden;
    box-shadow:0 10px 30px rgba(0,0,0,.18);
  }
  .brand{
    position:absolute;top:62px;left:0;width:100%;
    display:flex;flex-direction:column;align-items:center;gap:14px;
  }
  .brand-mark{width:58px;height:58px;border-radius:50%;border:3px solid var(--gold)}
  .brand-name{
    font-family:"Cormorant Garamond",serif;font-weight:600;font-size:30px;
    letter-spacing:2px;color:var(--gold);
  }
  .product-name{
    position:absolute;top:232px;left:30px;right:30px;text-align:center;
    font-family:"Titan One",sans-serif;font-size:96px;line-height:1;
    color:var(--white);letter-spacing:-1px;white-space:nowrap;
    text-shadow:0 3px 0 var(--crimson),0 6px 0 var(--crimson),0 9px 0 var(--crimson-dark),0 14px 16px rgba(0,0,0,.35);
  }
  .hero-visual{
    position:absolute;left:0;top:360px;width:100%;height:500px;
    background:
      radial-gradient(circle at 72% 58%, rgba(120,200,255,.9) 0%, rgba(70,150,235,.6) 30%, rgba(0,0,0,0) 55%),
      radial-gradient(circle at 22% 74%, #e6c38a 0%, #c99a55 25%, rgba(0,0,0,0) 48%),
      radial-gradient(ellipse 55% 45% at 55% 40%, rgba(210,150,200,.75) 0%, rgba(120,120,220,.4) 45%, rgba(0,0,0,0) 75%);
    -webkit-mask-image:linear-gradient(180deg,transparent 0%,#000 22%);
    mask-image:linear-gradient(180deg,transparent 0%,#000 22%);
  }
  .info-band{
    position:absolute;left:0;bottom:0;width:100%;height:150px;
    background:linear-gradient(180deg,rgba(31,34,38,.92),var(--band));
    display:flex;align-items:center;justify-content:space-between;padding:0 28px;
  }
  .contents{display:flex;flex-direction:column;gap:8px}
  .contents-pill{
    display:inline-block;padding:6px 22px;border-radius:26px;
    background:linear-gradient(90deg,var(--mint),var(--teal));
    font-family:"Roboto Condensed",sans-serif;font-weight:500;font-size:32px;color:var(--white);
  }
  .contents-yield{
    font-family:"Roboto Condensed",sans-serif;font-weight:500;font-size:21px;color:var(--white);padding-left:14px;
  }
  .eco-claims{display:flex;gap:12px;list-style:none}
  .eco-claim{display:flex;flex-direction:column;align-items:center;gap:6px;width:70px}
  .eco-claim svg{width:40px;height:40px;fill:none;stroke:var(--icon);stroke-width:2.2;stroke-linecap:round;stroke-linejoin:round}
  .eco-label{
    font-family:"Roboto Condensed",sans-serif;font-size:11px;color:var(--icon);
    text-align:center;white-space:nowrap;letter-spacing:.2px;
  }
</style>
</head>
<body>
  <main class="package-front">
    <header class="brand">
      <span class="brand-mark"></span>
      <span class="brand-name">LINDAVEL</span>
    </header>

    <h1 class="product-name">WASSTRIPS</h1>

    <div class="hero-visual" role="img" aria-label="Illustratie van opgevouwen handdoeken in een rieten wasmand naast een blauwe waterplons met zeepbellen"></div>

    <section class="info-band">
      <div class="contents">
        <span class="contents-pill">Bevat: 30 wasstrips</span>
        <span class="contents-yield">30 wasstrips = 60 wasbeurten</span>
      </div>
      <ul class="eco-claims">
        <li class="eco-claim">
          <svg viewBox="0 0 40 40"><circle cx="20" cy="20" r="2.5"/><ellipse cx="20" cy="20" rx="16" ry="6"/><ellipse cx="20" cy="20" rx="16" ry="6" transform="rotate(60 20 20)"/><ellipse cx="20" cy="20" rx="16" ry="6" transform="rotate(-60 20 20)"/></svg>
          <span class="eco-label">NEDERLANDS LAB</span>
        </li>
        <li class="eco-claim">
          <svg viewBox="0 0 40 40"><circle cx="20" cy="20" r="17"/><path d="M20 30V19"/><path d="M20 21c-6 0-8-4-8-8 5 0 8 3 8 8z"/><path d="M20 19c0-5 3-8 8-8 0 4-2 8-8 8z"/></svg>
          <span class="eco-label">PLANTAARDIG</span>
        </li>
        <li class="eco-claim">
          <svg viewBox="0 0 40 40"><path d="M12 16l5-8h6l3 5"/><path d="M23 13h4l-1-4"/><path d="M30 20l3 6-3 5h-7"/><path d="M25 28l-2 3 3 2"/><path d="M17 31h-7l-3-5 4-6"/><path d="M8 21l3-1 1 3"/></svg>
          <span class="eco-label">GEEN AFVAL</span>
        </li>
        <li class="eco-claim">
          <svg viewBox="0 0 40 40"><circle cx="20" cy="20" r="17"/><path d="M9 12c4 1 6 4 5 8s3 5 2 9"/><path d="M26 5c-2 4 1 6 4 7s4 5 2 8"/><path d="M22 30c2-3 6-3 8-1"/></svg>
          <span class="eco-label">ONZE PLANEET</span>
        </li>
      </ul>
    </section>
  </main>
</body>
</html>
```